Veldmark Supplies Business Card

Professional business card that stand out to our potential customers. Front and back with clean modern design

Industry/Entity Type

Oil and gas

Contact Information for Business Card

Name, address, website , office phone and cell number

Requirements
Must have
• Editable files for each employee

```html
<!DOCTYPE html>
<html lang="en">
<head>
<meta charset="utf-8">
<title>Veldmark Supplies Business Card</title>
<link rel="stylesheet" href="https://fonts.googleapis.com/css2?family=Montserrat:wght@400;700;800&family=Open+Sans:wght@400;600&display=swap">
<style>
  :root {
    --backdrop: #3a3a3c;
    --card-dark: #1c1c1d;
    --card-light: #ffffff;
    --accent-red: #ff0000;
    --accent-blue: #00b3d6;
    --text-light: #ffffff;
  }
  * { box-sizing: border-box; margin: 0; padding: 0; }
  html, body {
    width: 1200px; height: 1200px; overflow: hidden;
    background: var(--backdrop);
  }
  .canvas {
    width: 1200px; height: 1200px;
    display: flex; flex-direction: column; align-items: center; justify-content: center;
    gap: 60px;
  }
  .card {
    width: 900px; height: 514px;
    border-radius: 30px;
    overflow: hidden;
    position: relative;
    box-shadow: 0 5px 0 var(--accent-red), 0 18px 30px rgba(0,0,0,0.45);
  }
  /* front */
  .card-front { background: var(--card-dark); display: flex; flex-direction: column; }
  .front-top {
    flex: none; height: 232px; background: var(--card-light);
    border-bottom: 7px solid var(--accent-red);
    display: flex; align-items: center; justify-content: center;
  }
  .brand {
    display: flex; align-items: center; gap: 14px;
    font-family: "Montserrat", sans-serif; font-weight: 800;
    text-transform: uppercase; letter-spacing: 2px;
    color: var(--accent-red);
  }
  .brand-mark { background: var(--accent-red); flex: none; }
  .card-front .brand { font-size: 34px; margin-left: -120px; }
  .card-front .brand-mark { width: 30px; height: 30px; }
  .front-body {
    position: relative; flex: 1;
    padding: 30px 60px 34px;
    display: flex; justify-content: space-between; align-items: flex-end;
    font-family: "Open Sans", sans-serif; color: var(--text-light);
  }
  .divider {
    position: absolute; left: 60px; right: 60px; top: 112px;
    height: 2px; background: var(--accent-red);
  }
  .person-name {
    font-family: "Montserrat", sans-serif; font-weight: 700;
    color: var(--accent-red); font-size: 38px; line-height: 1; letter-spacing: 1px;
  }
  .person-title { font-size: 24px; line-height: 1.2; margin-top: 6px; letter-spacing: 1px; }
  .contact-list { list-style: none; font-size: 21px; line-height: 1.55; }
  .person .contact-list { margin-top: 34px; }
  .contact-list li { display: flex; align-items: center; gap: 12px; }
  .icon { width: 20px; height: 20px; flex: none; fill: var(--accent-red); }
  /* back */
  .card-back { background: var(--card-dark); display: flex; align-items: center; justify-content: center; }
  .card-back .brand { font-size: 54px; letter-spacing: 3px; }
  .card-back .brand-mark { width: 46px; height: 46px; }
</style>
</head>
<body>
<main class="canvas">
  <section class="card card-front">
    <div class="front-top">
      <div class="brand"><span class="brand-mark"></span>Veldmark Supplies</div>
    </div>
    <div class="front-body">
      <div class="divider"></div>
      <div class="person">
        <p class="person-name">FULL NAME</p>
        <p class="person-title">TITLE</p>
        <ul class="contact-list">
          <li><svg class="icon" viewBox="0 0 20 20"><path d="M6 1h8a2 2 0 0 1 2 2v14a2 2 0 0 1-2 2H6a2 2 0 0 1-2-2V3a2 2 0 0 1 2-2zm0 2v12h8V3z"/></svg>(000) 000 0000</li>
          <li><svg class="icon" viewBox="0 0 20 20"><path d="M4 1l4 4-2 3c1 2 3 4 6 6l3-2 4 4-3 3C9 19 1 11 1 4z"/></svg>(000) 000 0000</li>
          <li><svg class="icon" viewBox="0 0 20 20"><path d="M1 4h18v12H1zm2 2v.3l7 5 7-5V6zm0 2.7V14h14V8.7l-7 5z"/></svg>email@company.com</li>
        </ul>
      </div>
      <ul class="contact-list location">
        <li><svg class="icon" viewBox="0 0 20 20"><path d="M10 1a6 6 0 0 1 6 6c0 5-6 12-6 12S4 12 4 7a6 6 0 0 1 6-6zm0 3.5a2.5 2.5 0 1 0 0 5 2.5 2.5 0 0 0 0-5z"/></svg>123 Name Street, 000<br>Your City, 00000-000</li>
        <li><svg class="icon" viewBox="0 0 20 20"><path d="M10 1a9 9 0 1 1 0 18 9 9 0 0 1 0-18zm-1 2.1A7 7 0 0 0 3.1 9H7c.1-2.3.8-4.4 2-5.9zm2 0c1.2 1.5 1.9 3.6 2 5.9h3.9A7 7 0 0 0 11 3.1zM9 9h2c-.1-2-.5-3.6-1-4.6-.5 1-.9 2.6-1 4.6zm-5.9 2A7 7 0 0 0 9 16.9c-1.2-1.5-1.9-3.6-2-5.9zm6 0c.1 2 .5 3.6 1 4.6.5-1 .9-2.6 1-4.6zm3.9 0c-.1 2.3-.8 4.4-2 5.9a7 7 0 0 0 5.9-5.9z"/></svg>www.company.com</li>
      </ul>
    </div>
  </section>

  <section class="card card-back">
    <div class="brand"><span class="brand-mark"></span>Veldmark Supplies</div>
  </section>
</main>
</body>
</html>
```